New Business Card Design Project

We require a business card design for Vexalund, a newly established Indian company.
Our focus is on the development, manufacturing, and export of a diverse array of pharmaceutical products on a global scale. The card should convey a professional appearance, as our primary markets are in Africa, China, and Southeast Asian nations.
We envision a two-sided business card, with the reverse side dedicated to a logo set against a solid color or an elegantly designed pattern. The corners should be rounded. We would appreciate seeing both horizontal and vertical design options. We trust the designer to utilize their expertise in creating this design.

The content for the business card is included in the attached Word file.

Target Market(s)

Our primary markets are in Africa, China, and Southeast Asian, Latin America, Maldives, Sri Lanka

Industry/Entity Type

Pharmaceutical Manufacturing and Export

Contact Information for Business Card

Colors

Designer to choose colors to be used in the design.

Requirements
Must have
• The reverse side of the business card features solely the logo along with the tagline, "Care in Every Dose."
Should not have
• The logo should not exceed two instances, encompassing both the front and back sides of the card.

```html
<!DOCTYPE html>
<html lang="en">
<head>
<meta charset="utf-8">
<title>Vexalund Business Card</title>
<link rel="stylesheet" href="https://fonts.googleapis.com/css2?family=Montserrat:wght@300;400;700;800&family=Open+Sans:wght@400;600&family=Poppins:wght@400&display=swap">
<style>
  :root {
    --stage: #232325;
    --coral: #f0644f;
    --coral-edge: #d9503d;
    --ink: #222226;
    --blue: #2ba3dc;
    --white: #ffffff;
    --soft-white: #ecebea;
  }
  * { box-sizing: border-box; margin: 0; padding: 0; }
  html, body {
    width: 1200px;
    height: 711px;
    overflow: hidden;
    background: var(--stage);
  }
  .stage {
    position: relative;
    width: 1200px;
    height: 711px;
  }
  .card {
    position: absolute;
    top: 205px;
    width: 520px;
    height: 300px;
    border-radius: 24px;
    overflow: hidden;
  }
  /* Logo side */
  .card--logo {
    left: 50px;
    background: var(--coral);
    display: flex;
    flex-direction: column;
    align-items: center;
    justify-content: center;
  }
  .brand {
    display: flex;
    align-items: center;
    gap: 12px;
    font-family: "Montserrat", sans-serif;
    font-weight: 800;
    font-size: 58px;
    letter-spacing: -0.5px;
    color: var(--white);
  }
  .brand__dot {
    width: 22px;
    height: 22px;
    border-radius: 50%;
    background: var(--white);
  }
  .tagline {
    margin-top: 14px;
    font-family: "Poppins", sans-serif;
    font-size: 14px;
    letter-spacing: 0.6px;
    color: var(--white);
  }
  /* Contact side */
  .card--contact {
    left: 630px;
    background: var(--ink);
    border: 2px solid var(--coral-edge);
  }
  .contact-brand {
    position: absolute;
    left: 22px;
    top: 112px;
    display: flex;
    align-items: center;
    gap: 8px;
    font-family: "Montserrat", sans-serif;
    font-weight: 800;
    font-size: 36px;
    color: var(--blue);
  }
  .contact-brand__dot {
    width: 14px;
    height: 14px;
    border-radius: 50%;
    background: var(--blue);
  }
  .divider {
    position: absolute;
    left: 248px;
    top: 62px;
    width: 1px;
    height: 150px;
    background: var(--blue);
  }
  .person {
    position: absolute;
    left: 272px;
    top: 62px;
    font-family: "Montserrat", sans-serif;
  }
  .person__name {
    font-size: 22px;
    line-height: 1.1;
    white-space: nowrap;
  }
  .person__first { font-weight: 800; color: var(--blue); }
  .person__last { font-weight: 300; color: var(--coral); }
  .person__role {
    margin-top: 2px;
    margin-left: 16px;
    font-family: "Open Sans", sans-serif;
    font-size: 13px;
    color: var(--soft-white);
  }
  .contact-list {
    position: absolute;
    left: 288px;
    top: 132px;
    list-style: none;
    font-family: "Open Sans", sans-serif;
    font-size: 12.5px;
    color: var(--soft-white);
  }
  .contact-list li {
    display: flex;
    align-items: center;
    gap: 9px;
    height: 22px;
    white-space: nowrap;
  }
  .contact-list svg { width: 14px; height: 14px; flex: none; }
  .address {
    position: absolute;
    left: 0;
    right: 0;
    bottom: 28px;
    text-align: center;
    font-family: "Open Sans", sans-serif;
    font-size: 13px;
    letter-spacing: 0.3px;
    color: var(--soft-white);
  }
</style>
</head>
<body>
<main class="stage">

  <section class="card card--logo" aria-label="Card logo side">
    <div class="brand"><span class="brand__dot"></span>Vexalund</div>
    <p class="tagline">Care in Every Dose.</p>
  </section>

  <section class="card card--contact" aria-label="Card contact side">
    <div class="contact-brand"><span class="contact-brand__dot"></span>Vexalund</div>
    <span class="divider"></span>

    <div class="person">
      <p class="person__name"><span class="person__first">Rohan</span> <span class="person__last">K. Mehra</span></p>
      <p class="person__role">CEO</p>
    </div>

    <ul class="contact-list">
      <li>
        <svg viewBox="0 0 14 14"><rect x="3.5" y="1" width="7" height="12" rx="1.5" fill="none" stroke="var(--coral)" stroke-width="1.5"/></svg>
        +919 412857306
      </li>
      <li>
        <svg viewBox="0 0 14 14"><circle cx="7" cy="7" r="6" fill="none" stroke="var(--blue)" stroke-width="1.3"/><ellipse cx="7" cy="7" rx="2.6" ry="6" fill="none" stroke="var(--blue)" stroke-width="1"/><line x1="1" y1="7" x2="13" y2="7" stroke="var(--blue)" stroke-width="1"/></svg>
        www.vexalund.com
      </li>
      <li>
        <svg viewBox="0 0 14 14"><rect x="1" y="3" width="12" height="9" rx="1" fill="none" stroke="var(--coral)" stroke-width="1.4"/><polyline points="1.5,3.5 7,8 12.5,3.5" fill="none" stroke="var(--coral)" stroke-width="1.4"/></svg>
        rmehra@vexalund.com
      </li>
    </ul>

    <p class="address">12, Lotus Colony, Amravati, 444601, India</p>
  </section>

</main>
</body>
</html>
```